Modern, high quality Surfing Earplug company

New Zealand based and inspired, Surfing Eaplugs for USA Online Banner Advert campaign. We require a simple - wow factor banner advert that communicates the surfing and beach lifestyle, rather than a total product focus.

A design that can incorporate all three people from these pics is desirable. The VORN logo should always be in capitals, in the Anurati font, and in black or reverse white. The tagline is "Protect Your Ears, Surf for a Lifetime"
Nothing too fancy please. It must be optimized for the web
Updates

Hello all,thanks for so many great efforts! Please note the following banner sizes will be needed for Desktop, Tablet and Mobile phone 300 x 600 320 x 50 300 x 250 728 x 90 970 x 90 Thanks Dale

Target Market(s)

25 to 50 year old male and female surfers and swimmers in the USA

Industry/Entity Type

It Company

Font styles to use
Sans Serif

Colors
3276b5
33a6d7
ffc623
fbed22
ec1f27

Requirements
Must have
• VORN logo: either in black or white reverse.
• Tagline: "Protect your Ears - Surf for a Lifetime' exactly how it's written here
• Be optimized for the web
Nice to have
• All the people on the brief included. I'm not too concerned if not possible, but must be at least 2 males and 1 female
• Simple, clean and strong!
• A sunrise or sunset, nice blue waves on the beach for effect
Should not have
• Overcrowded design elements

```html
<!DOCTYPE html>
<html lang="en">
<head>
<meta charset="utf-8">
<title>VORN Surf Earplugs – Banner Set</title>
<link href="https://fonts.googleapis.com/css2?family=Bebas+Neue&family=Roboto:wght@700&display=swap" rel="stylesheet">
<style>
:root{
  --stage-light:#ffffff;
  --stage-dark:#c9c9c9;
  --sky:#e8e6f4;
  --sea-light:#b4d6e8;
  --sea-mid:#7cc0e0;
  --sea-deep:#33a6d7;
  --sea-navy:#3276b5;
  --ink:#1e2633;
  --white:#ffffff;
  --ring-yellow:#ffc623;
  --ring-red:#ec1f27;
  --wetsuit:rgba(34,40,48,.88);
  --wetsuit-soft:rgba(34,40,48,.45);
  --plug-green:#6fe04a;
  --skin:#c48f6a;
  --hair:#5a3a28;
}
*{margin:0;padding:0;box-sizing:border-box}
html,body{width:1200px;height:800px;overflow:hidden}
body{
  background:linear-gradient(135deg,var(--stage-dark) 0%,var(--stage-light) 45%,var(--stage-dark) 100%);
  position:relative;font-family:"Bebas Neue",sans-serif;
}
.size-label{position:absolute;font-family:"Roboto",sans-serif;font-weight:700;font-size:24px;color:#000;line-height:1;transform:translateX(-50%)}
.banner{position:absolute;overflow:hidden;
  background:linear-gradient(180deg,var(--sky) 0%,var(--sea-light) 45%,var(--sea-mid) 70%,var(--sea-deep) 100%)}
.banner--leader{background:linear-gradient(90deg,#4a93b8 0%,var(--sea-mid) 30%,var(--sea-light) 60%,#dfe9ee 78%,#a9c3cf 100%)}
.photo-surf{position:absolute}
.photo-surf--figure{
  background:
    radial-gradient(ellipse 42% 14% at 52% 10%,rgba(196,150,120,.75) 0%,rgba(196,150,120,0) 100%),
    radial-gradient(ellipse 55% 48% at 55% 52%,var(--wetsuit) 0%,var(--wetsuit-soft) 60%,rgba(34,40,48,0) 100%);
}
.photo-surf--wave{
  background:
    radial-gradient(ellipse 60% 45% at 30% 35%,rgba(255,255,255,.75) 0%,rgba(255,255,255,0) 100%),
    linear-gradient(180deg,rgba(120,150,160,.2) 0%,rgba(70,110,120,.45) 100%);
}
.photo-circle{position:absolute;border-radius:50%}
.photo-circle--plugs{border:5px solid var(--ring-yellow);
  background:radial-gradient(circle at 30% 62%,var(--plug-green) 0%,rgba(111,224,74,.6) 25%,#b6c4bd 55%,#dfe3e6 100%)}
.photo-circle--smile{border:5px solid var(--ring-red);
  background:radial-gradient(circle at 68% 45%,var(--skin) 0%,#a87452 45%,var(--hair) 80%,#3d2a20 100%)}
.txt{position:absolute;line-height:1;white-space:nowrap;font-family:"Bebas Neue",sans-serif}
.txt--white{color:var(--white)}
.txt--dark{color:var(--ink)}
.brand{position:absolute;line-height:1;color:var(--ink);font-family:"Bebas Neue",sans-serif;letter-spacing:.08em;white-space:nowrap}
</style>
</head>
<body>

<!-- 728x90 -->
<div class="size-label" style="left:179px;top:80px">728x90</div>
<div class="banner banner--leader" style="left:240px;top:47px;width:720px;height:89px">
  <div class="photo-surf photo-surf--wave" role="img" aria-label="Breaking ocean wave" style="left:420px;top:0;width:300px;height:89px"></div>
  <div class="photo-surf photo-surf--figure" role="img" aria-label="Surfer in a wetsuit in the waves" style="left:584px;top:0;width:136px;height:89px"></div>
  <div class="brand" style="left:4px;top:26px;font-size:50px;letter-spacing:.04em">VORN</div>
  <div class="txt txt--white" style="left:106px;top:9px;font-size:55px">PROTECT</div>
  <div class="txt txt--dark" style="left:106px;top:53px;font-size:37px">YOUR EARS</div>
  <div class="txt txt--white" style="left:280px;top:9px;font-size:55px">SURF</div>
  <div class="txt txt--dark" style="left:262px;top:54px;font-size:33px">FOR A LIFETIME</div>
  <div class="photo-circle photo-circle--plugs" role="img" aria-label="Green surf earplugs" style="left:434px;top:2px;width:84px;height:84px"></div>
</div>

<!-- 160x600 -->
<div class="size-label" style="left:92px;top:218px">160x600</div>
<div class="banner" style="left:28px;top:238px;width:128px;height:480px">
  <div class="photo-surf photo-surf--figure" role="img" aria-label="Surfer in a wetsuit standing in the sea" style="left:0;top:0;width:128px;height:300px"></div>
  <div class="photo-circle photo-circle--plugs" role="img" aria-label="Green surf earplugs" style="left:14px;top:90px;width:96px;height:96px"></div>
  <div class="photo-circle photo-circle--smile" role="img" aria-label="Smiling woman holding an earplug" style="left:16px;top:196px;width:96px;height:96px"></div>
  <div class="txt txt--white" style="left:4px;top:306px;font-size:46px">PROTECT</div>
  <div class="txt txt--dark" style="left:16px;top:343px;font-size:29px">YOUR EARS</div>
  <div class="txt txt--white" style="left:26px;top:365px;font-size:45px">SURF</div>
  <div class="txt txt--dark" style="left:6px;top:403px;font-size:26px">FOR A LIFETIME</div>
  <div class="brand" style="left:16px;top:433px;font-size:46px">VORN</div>
</div>

<!-- 300x250 -->
<div class="size-label" style="left:458px;top:280px">300x250</div>
<div class="banner" style="left:270px;top:326px;width:354px;height:294px">
  <div class="photo-surf photo-surf--figure" role="img" aria-label="Surfer in a wetsuit standing in the sea" style="left:226px;top:0;width:128px;height:294px"></div>
  <div class="photo-circle photo-circle--plugs" role="img" aria-label="Green surf earplugs" style="left:13px;top:4px;width:128px;height:128px"></div>
  <div class="photo-circle photo-circle--smile" role="img" aria-label="Smiling woman holding an earplug" style="left:192px;top:102px;width:124px;height:124px"></div>
  <div class="txt txt--white" style="left:8px;top:134px;font-size:57px">PROTECT</div>
  <div class="txt txt--dark" style="left:22px;top:182px;font-size:39px">YOUR EARS</div>
  <div class="txt txt--white" style="left:38px;top:210px;font-size:59px">SURF</div>
  <div class="txt txt--dark" style="left:8px;top:259px;font-size:35px">FOR A LIFETIME</div>
  <div class="brand" style="left:198px;top:232px;font-size:56px;letter-spacing:.05em">VORN</div>
</div>

<!-- 336x280 -->
<div class="size-label" style="left:844px;top:261px">336x280</div>
<div class="banner" style="left:651px;top:298px;width:388px;height:322px">
  <div class="photo-surf photo-surf--figure" role="img" aria-label="Surfer in a wetsuit standing in the sea" style="left:225px;top:0;width:163px;height:322px"></div>
  <div class="photo-circle photo-circle--plugs" role="img" aria-label="Green surf earplugs" style="left:36px;top:7px;width:132px;height:132px"></div>
  <div class="photo-circle photo-circle--smile" role="img" aria-label="Smiling woman holding an earplug" style="left:227px;top:120px;width:140px;height:140px"></div>
  <div class="txt txt--white" style="left:23px;top:143px;font-size:63px">PROTECT</div>
  <div class="txt txt--dark" style="left:38px;top:195px;font-size:41px">YOUR EARS</div>
  <div class="txt txt--white" style="left:54px;top:227px;font-size:63px">SURF</div>
  <div class="txt txt--dark" style="left:23px;top:280px;font-size:39px">FOR A LIFETIME</div>
  <div class="brand" style="left:243px;top:266px;font-size:60px;letter-spacing:.05em">VORN</div>
</div>

</body>
</html>
```